Real estate broker business card

Want a modern celan but effective business card for my residential and commercial real estate business. I want the back of the card to advertise my services and to capture business. I have attached the back of my current business card fore ideas
Updates

Logos, photo and text updates added! Added Saturday, September 3, 2016

Project Deadline Extended Reason: LOGOS, PHOTOS AND TEST JUST UPLOADED! I'M READY TO PICK A DESIGN! THANK YOU! Added Saturday, September 3, 2016

Target Market(s)

home buyers and seller. commercial buyers and sellers

Industry/Entity Type

Real Estate

Contact Information for Business Card

must have my contact information and my photo

Requirements
Must have
• Carla Ventrino
• Owner & Qualifying Broker
• Ventrino Real Estate Services
• 505.718.2094
• carla@ventrinohomes.example
• www.ventrinohomes.example
Nice to have
• metallic
• Business capture text: " Don't buy or lease property without someone looking out for your best interests. I will represent you on your home or investment purchase for FREE!"
• "Home owners, call today to receive a FREE market analysis for your homes value!

```html
<!DOCTYPE html>
<html lang="en">
<head>
<meta charset="utf-8">
<title>Ventrino Real Estate Services – Business Card</title>
<link href="https://fonts.googleapis.com/css2?family=Cinzel:wght@500&family=Marcellus&display=swap" rel="stylesheet">
<style>
  :root {
    --stage: #7a7a7a;
    --stage-dark: #4a4a4a;
    --teal: #127f8c;
    --teal-deep: #0b5f6b;
    --teal-light: #1ea3b0;
    --white: #ffffff;
    --silver: #c9ccd0;
    --ink-teal: #0f7d89;
  }
  * { box-sizing: border-box; margin: 0; padding: 0; }
  html, body { width: 1200px; height: 950px; overflow: hidden; }
  body {
    background: radial-gradient(ellipse at 50% 45%, var(--stage) 0%, var(--stage-dark) 100%);
    position: relative;
    font-family: "Marcellus", "Optima", serif;
  }
  .card {
    position: absolute;
    width: 700px;
    height: 400px;
    border-radius: 4px;
    overflow: hidden;
    box-shadow: 0 14px 30px rgba(0,0,0,0.45);
  }

  /* Back of card */
  .card-back { left: 90px; top: 70px; }
  .card-back .pattern-field {
    position: absolute; inset: 0;
    background: radial-gradient(ellipse at 50% 50%, var(--teal-light) 0%, var(--teal) 55%, var(--teal-deep) 100%);
  }
  .card-back .back-content {
    position: absolute; inset: 0;
    display: flex; flex-direction: column; align-items: center; justify-content: center;
    color: var(--white); text-align: center;
  }
  .brand-name {
    font-family: "Cinzel", "Trajan Pro", serif;
    font-weight: 500;
    color: var(--white);
    font-size: 34px;
    letter-spacing: 2px;
    line-height: 1.15;
  }
  .back-offer {
    margin-top: 14px;
    font-size: 19px;
    line-height: 1.35;
  }

  /* Front of card */
  .card-front { left: 410px; top: 480px; background: var(--white); }
  .card-front svg.front-bg { position: absolute; inset: 0; }
  .agent-photo {
    position: absolute; left: 42px; top: 46px;
    width: 170px; height: 168px; border-radius: 10px;
    background: linear-gradient(160deg, #3d4a34 0%, #5b4a3e 45%, #c9b9aa 100%);
  }
  .agent-details {
    position: absolute; left: 42px; top: 232px;
    color: var(--white);
  }
  .agent-name {
    font-family: "Cinzel", "Trajan Pro", serif;
    font-weight: 500; font-size: 23px; letter-spacing: 1px;
  }
  .agent-role { font-size: 16px; line-height: 1.35; margin-top: 2px; }
  .contact-list { list-style: none; margin-top: 12px; font-size: 15px; }
  .contact-list li { display: flex; align-items: center; gap: 9px; line-height: 1.5; }
  .contact-list svg { width: 14px; height: 14px; flex: none; }
  .front-brand {
    position: absolute; left: 400px; top: 118px; width: 260px;
    display: flex; align-items: center; gap: 12px;
  }
  .front-brand .brand-mark {
    width: 38px; height: 38px; border-radius: 50%;
    background: var(--ink-teal); flex: none;
  }
  .front-brand .brand-name { color: var(--ink-teal); font-size: 22px; letter-spacing: 1.5px; }
</style>
</head>
<body>

  <section class="card card-back" aria-label="Business card back">
    <div class="pattern-field" role="img" aria-label="Teal background with a faint repeating brand pattern"></div>
    <div class="back-content">
      <div class="brand-name">VENTRINO<br>REAL ESTATE SERVICES</div>
      <p class="back-offer">Home owners, call today to receive a<br>FREE market analysis for your homes value!</p>
    </div>
  </section>

  <section class="card card-front" aria-label="Business card front">
    <svg class="front-bg" viewBox="0 0 700 400" width="700" height="400" aria-hidden="true">
      <defs>
        <linearGradient id="tealField" x1="0" y1="0" x2="1" y2="1">
          <stop offset="0" stop-color="#1a97a4"/>
          <stop offset="1" stop-color="#0b6470"/>
        </linearGradient>
        <linearGradient id="silverRibbon" x1="0" y1="0" x2="1" y2="0">
          <stop offset="0" stop-color="#8e9399"/>
          <stop offset="0.5" stop-color="#f4f5f6"/>
          <stop offset="1" stop-color="#a9adb2"/>
        </linearGradient>
      </defs>
      <rect width="700" height="400" fill="url(#tealField)"/>
      <path d="M282 0 C232 125 402 238 488 400 L516 400 C428 232 258 120 306 0 Z" fill="url(#silverRibbon)"/>
      <path d="M304 0 C254 122 424 232 514 400 L700 400 L700 0 Z" fill="#ffffff"/>
    </svg>

    <div class="agent-photo" role="img" aria-label="Portrait photo of the broker"></div>

    <div class="agent-details">
      <div class="agent-name">CARLA VENTRINO</div>
      <div class="agent-role">Owner &amp; Qualifying Broker<br>Ventrino Real Estate Services</div>
      <ul class="contact-list">
        <li><svg viewBox="0 0 16 16"><path fill="#fff" d="M3.5 1 L6 1 L7 4.5 L5.3 6 C6.2 8 8 9.8 10 10.7 L11.5 9 L15 10 L15 12.5 C15 13.9 13.9 15 12.5 15 C6.7 15 1 9.3 1 3.5 C1 2.1 2.1 1 3.5 1Z"/></svg>505.718.2094</li>
        <li><svg viewBox="0 0 16 16"><rect x="1" y="3" width="14" height="10" fill="#fff"/><path d="M1.5 3.5 L8 9 L14.5 3.5" fill="none" stroke="#127f8c" stroke-width="1.4"/></svg>carla@ventrinohomes.example</li>
        <li><svg viewBox="0 0 16 16"><circle cx="8" cy="8" r="6.5" fill="none" stroke="#fff" stroke-width="1.5"/><ellipse cx="8" cy="8" rx="2.8" ry="6.5" fill="none" stroke="#fff" stroke-width="1.2"/><path d="M1.5 8 H14.5" stroke="#fff" stroke-width="1.2"/></svg>www.ventrinohomes.example</li>
      </ul>
    </div>

    <div class="front-brand">
      <span class="brand-mark" aria-hidden="true"></span>
      <div class="brand-name">VENTRINO<br>REAL ESTATE SERVICES</div>
    </div>
  </section>

</body>
</html>
```